Vorn upkeep KT Solar Venture

Solar power system install
Services and maintenance
wiring, Rewinding and Renovation
Switch Board Upgrade
Power and lighting point
t doesn’t matter how much you spend on quality parts, your solar system will let you down if your design and installation are sub-par. Have your solar system tailored and installed by our Master Electrician and Bright Grid Guild Accredited team.

Target Market(s)

sales and installed

Industry/Entity Type

Solar install and retailer

Contact Information for Business Card

Name , Email, Phone Number ,Business address,

Font styles to use
Serif

Colors
0054AA
0677BA
7BADD7
CADEEF
E8F1F8

Requirements
Must have
• clear and bright
Nice to have
• new design
Should not have
• unclear pictures

```html
<!DOCTYPE html>
<html lang="en">
<head>
<meta charset="utf-8">
<title>KT Solar Venture – Business Card</title>
<link href="https://fonts.googleapis.com/css2?family=Roboto:wght@400;500;700&family=Roboto+Condensed:wght@700&display=swap" rel="stylesheet">
<style>
  :root {
    --backdrop: #2d2d2d;
    --card: #f1f1f1;
    --card-edge: #e2e2e2;
    --brand-blue: #0054AA;
    --mid-blue: #0677BA;
    --leaf-green: #5aa63a;
    --deep-green: #1f8a3c;
    --ink: #1c1c1c;
    --band-text: #eef6ee;
  }
  * { margin: 0; padding: 0; box-sizing: border-box; }
  html, body { width: 1200px; height: 1138px; overflow: hidden; }
  body {
    background: var(--backdrop);
    font-family: "Roboto", Arial, sans-serif;
    position: relative;
  }
  .card {
    position: absolute;
    width: 622px;
    height: 375px;
    border-radius: 16px;
    background: linear-gradient(180deg, #f6f6f6 0%, var(--card) 60%, var(--card-edge) 100%);
    overflow: hidden;
  }
  .card--front { left: 274px; top: 186px; }
  .card--back { left: 276px; top: 608px; }

  .brand { position: absolute; display: flex; align-items: center; gap: 18px; }
  .brand__dot { border-radius: 50%; background: var(--mid-blue); flex: none; }
  .brand__name {
    font-family: "Roboto Condensed", "Arial Narrow", sans-serif;
    font-weight: 700;
    color: var(--brand-blue);
    line-height: 1.08;
    letter-spacing: 0.5px;
  }
  .card--front .brand { left: 120px; top: 60px; }
  .card--front .brand__dot { width: 96px; height: 96px; }
  .card--front .brand__name { font-size: 35px; }

  .services-band {
    position: absolute;
    left: 0; top: 239px;
    width: 100%; height: 73px;
    background: linear-gradient(90deg, #6aab3a 0%, #3f9a72 45%, #0677BA 85%, #0a6fb0 100%);
    display: flex; flex-direction: column; justify-content: center; align-items: center;
    gap: 5px;
    color: var(--band-text);
    font-size: 16px;
    letter-spacing: 0.1px;
  }
  .web-line {
    position: absolute; left: 0; top: 332px; width: 100%;
    text-align: center; font-size: 16px; color: var(--ink);
  }
  .rule { position: absolute; top: 343px; height: 2px; width: 78px; }
  .rule--blue { left: 112px; background: linear-gradient(90deg, transparent, var(--mid-blue)); }
  .rule--green { left: 432px; background: linear-gradient(90deg, var(--leaf-green), transparent); }

  .edge-tab {
    position: absolute; left: -36px; top: 46px;
    width: 48px; height: 76px; border-radius: 50%;
    background: linear-gradient(180deg, var(--leaf-green), var(--mid-blue));
  }
  .person { position: absolute; left: 34px; top: 56px; }
  .person__name { font-size: 26px; font-weight: 500; color: var(--brand-blue); line-height: 1.1; }
  .person__role { font-size: 16px; color: var(--ink); margin-top: 4px; }
  .address { position: absolute; left: 34px; top: 218px; font-size: 16px; line-height: 24px; color: var(--ink); }
  .contacts { position: absolute; left: 34px; top: 272px; list-style: none; font-size: 16px; color: var(--ink); }
  .contacts li { display: flex; align-items: center; height: 24px; }
  .contacts svg { width: 14px; height: 14px; margin-left: 0; margin-right: 18px; fill: var(--deep-green); }

  .card--back .brand { right: 40px; top: 250px; flex-direction: column; align-items: center; gap: 14px; }
  .card--back .brand__dot { width: 110px; height: 110px; }
  .card--back .brand__name { font-size: 32px; text-align: center; }
</style>
</head>
<body>
  <section class="card card--front">
    <div class="brand">
      <span class="brand__dot"></span>
      <div class="brand__name">VORN UPKEEP<br>KT SOLAR VENTURE</div>
    </div>
    <div class="services-band">
      <p>Solar Power System Install &nbsp;|&nbsp; Wiring, Rewinding &amp; Renovation</p>
      <p>Services &amp; Maintenance &nbsp;|&nbsp; Switch Board Upgrade &nbsp;|&nbsp; Power &amp; Lighting Point</p>
    </div>
    <span class="rule rule--blue"></span>
    <p class="web-line">www.ktsolarventure.com</p>
    <span class="rule rule--green"></span>
  </section>

  <section class="card card--back">
    <span class="edge-tab"></span>
    <div class="person">
      <p class="person__name">Aria Venn Holt</p>
      <p class="person__role">Managing Director</p>
    </div>
    <p class="address">58 Lindell Rd., Marrow City,<br>Fairdale, US 204816</p>
    <ul class="contacts">
      <li><svg viewBox="0 0 16 16" aria-hidden="true"><path d="M2 6c0-2 2-3 6-3s6 1 6 3v1h-3V5.5H5V7H2zM4 8h8l2 5H2z"/></svg>555-014-2290</li>
      <li><svg viewBox="0 0 16 16" aria-hidden="true"><path d="M1 3h14v10H1zM2.5 4.5 8 9l5.5-4.5v-.2H2.5z"/></svg>aria@ktsolarventure.com</li>
      <li><svg viewBox="0 0 16 16" aria-hidden="true"><path d="M8 1a7 7 0 1 0 0 14A7 7 0 0 0 8 1zm0 1.5c.8 0 1.7 1.6 2 4H6c.3-2.4 1.2-4 2-4zM3 7.5h2a12 12 0 0 0 0 1H3zm8 0h2v1h-2zM6 9.5h4c-.3 2.4-1.2 4-2 4s-1.7-1.6-2-4z"/></svg>www.ktsolarventure.com</li>
    </ul>
    <div class="brand">
      <span class="brand__dot"></span>
      <div class="brand__name">VORN UPKEEP<br>KT SOLAR VENTURE</div>
    </div>
  </section>
</body>
</html>
```